BOLD & MINIMALIST DESIGN NEEDED

We want a very bold but minimalistic business card design that is impactful and utilizes both sides of the business card. Our current logo is included for your use.

We want bold fonts and good use of negative space. We don't want the logo to overpower the design.

Target Market(s)

Professionals who are building new commercial buildings.

Industry/Entity Type

Construction

Contact Information for Business Card

Name, Title, email, office phone, cell phone, website

Font styles to use
Serif
Sans Serif

Requirements
Must have
• Bold design!

```html
<!DOCTYPE html>
<html lang="en">
<head>
<meta charset="utf-8">
<title>Ridgecrest Business Card</title>
<link href="https://fonts.googleapis.com/css2?family=Arimo:wght@400;700&display=swap" rel="stylesheet">
<style>
  :root {
    --backdrop: #dcdcdc;
    --paper: #f4f4f5;
    --ink: #111111;
    --text: #222222;
    --green: #82bb26;
    --green-light: #aad46e;
    --green-edge: #7cb724;
  }
  * { box-sizing: border-box; margin: 0; padding: 0; }
  html, body {
    width: 1200px; height: 1040px; overflow: hidden;
    background: var(--backdrop);
    font-family: "Arimo", Arial, sans-serif;
    color: var(--text);
  }
  .card {
    position: absolute; left: 276px; width: 648px; height: 370px;
    border-radius: 18px; overflow: hidden;
    box-shadow: 0 3px 6px rgba(0,0,0,.25);
  }
  .card-front { top: 125px; background: var(--paper); }
  .card-back {
    top: 565px;
    background: radial-gradient(ellipse at 50% 42%, var(--green-light) 0%, #98c850 40%, var(--green-edge) 100%);
  }

  .brand {
    position: absolute; right: 42px; top: 108px;
    display: flex; align-items: center; gap: 10px;
  }
  .brand-square { width: 22px; height: 22px; background: var(--green); }
  .brand-name {
    font-weight: 700; font-size: 34px; color: var(--ink); letter-spacing: 0.5px;
  }

  .person { position: absolute; left: 45px; top: 205px; }
  .person-name { font-weight: 700; font-size: 26px; color: var(--ink); letter-spacing: 0.3px; line-height: 1; }
  .person-title { font-size: 16px; color: var(--green); margin-top: 6px; }

  .divider { position: absolute; left: 45px; right: 42px; top: 256px; height: 1px; background: #333; }

  .contact-list { position: absolute; left: 45px; top: 268px; list-style: none; }
  .contact-list li {
    display: flex; align-items: center; gap: 8px;
    font-size: 16px; line-height: 20px; color: var(--text);
  }
  .contact-list svg { width: 12px; height: 12px; fill: var(--ink); flex: none; }

  .address {
    position: absolute; right: 42px; top: 270px; text-align: right;
    font-size: 16px; line-height: 20px; color: var(--text); font-style: normal;
  }

  .edge-green { position: absolute; left: 0; right: 0; bottom: 20px; height: 3px; background: var(--green); }
  .edge-black { position: absolute; left: 0; right: 0; bottom: 0; height: 17px; background: var(--ink); }

  .back-brand {
    position: absolute; left: 0; right: 0; top: 118px;
    display: flex; justify-content: center; align-items: center; gap: 16px;
  }
  .back-brand .brand-square { width: 40px; height: 40px; background: var(--ink); }
  .back-brand .brand-name { font-size: 64px; }
  .back-url {
    position: absolute; left: 0; right: 0; top: 312px; text-align: center;
    font-size: 15px; color: #2a2a2a;
  }
</style>
</head>
<body>
  <section class="card card-front">
    <div class="brand">
      <span class="brand-square"></span>
      <span class="brand-name">RIDGECREST</span>
    </div>

    <div class="person">
      <p class="person-name">DANIEL HARPER</p>
      <p class="person-title">President</p>
    </div>

    <div class="divider"></div>

    <ul class="contact-list">
      <li>
        <svg viewBox="0 0 24 24"><path d="M6.6 10.8a15 15 0 0 0 6.6 6.6l2.2-2.2c.3-.3.7-.4 1-.2 1.1.4 2.3.6 3.6.6.6 0 1 .4 1 1V20c0 .6-.4 1-1 1A17 17 0 0 1 3 4c0-.6.4-1 1-1h3.5c.6 0 1 .4 1 1 0 1.3.2 2.5.6 3.6.1.3 0 .7-.2 1z"/></svg>
        (555) 0142-7788
      </li>
      <li>
        <svg viewBox="0 0 24 24"><path d="M2 5h20v14H2z M4 7v.5l8 5 8-5V7l-8 5z" fill-rule="evenodd"/></svg>
        info@ridgecrest.com
      </li>
      <li>
        <svg viewBox="0 0 24 24"><circle cx="12" cy="12" r="10"/><path d="M2 12h20M12 2c3 3 3 17 0 20M12 2c-3 3-3 17 0 20" stroke="#f4f4f5" stroke-width="1.6" fill="none"/></svg>
        www.ridgecrest.com
      </li>
    </ul>

    <address class="address">
      4127 Alder Crest Road<br>
      Maple Glen, NY 11590
    </address>

    <div class="edge-green"></div>
    <div class="edge-black"></div>
  </section>

  <section class="card card-back">
    <div class="back-brand">
      <span class="brand-square"></span>
      <span class="brand-name">RIDGECREST</span>
    </div>
    <p class="back-url">www.ridgecrest.com</p>
  </section>
</body>
</html>
```